Brookvale Estates LLC stationary for a real estate property management company.

Create stationary (letterhead, envelopes, business cards) using Brookvale Estates LLC logo as primary creative element. Stationary design needs to be horizontal, leaving as much space as possible for correspondence copy. See attached Creative Brief and past stationary files for details.

Target Market(s)

Prospective apartment residents and current residents, vendors, and government agencies.

Industry/Entity Type

Property Management

Contact Information for Business Card

Business card employee title: Property Manager. Should include address, phone, fax, email, website, slogan, and Brookvale Estates logo.

Font styles to use
Sans Serif

Colors
0592cd
000000

Requirements
Must have
• Tone should be conservative, institutional, business (i.e. banking, finance, real estate). Must include: address, phone, fax, website, and slogan (see attached Creative Brief). Should be a horizontal design, leaving as much room as possible for letter correspondence copy.
Nice to have
• Please use an Arial or Helvetica style font.
Should not have
• Letterhead layout should leave as much room as possible for copy.

```html
<!DOCTYPE html>
<html lang="en">
<head>
<meta charset="utf-8">
<title>Brookvale Estates LLC — Business Card</title>
<link rel="stylesheet" href="https://fonts.googleapis.com/css2?family=Arimo:wght@400;700&display=swap">
<style>
  :root {
    --backdrop: #262626;
    --card-white: #fbfbfb;
    --brand-blue: #0592cd;
    --label-blue: #0a6fae;
    --text-gray: #4a4a4a;
    --title-gray: #666666;
    --slate-light: #6c6c70;
    --slate-dark: #38383a;
    --mark-white: #ffffff;
  }
  * { margin: 0; padding: 0; box-sizing: border-box; }
  html, body {
    width: 1200px;
    height: 960px;
    overflow: hidden;
    background: var(--backdrop);
    font-family: "Arimo", Arial, Helvetica, sans-serif;
  }
  .stage {
    position: relative;
    width: 1200px;
    height: 960px;
  }
  .card {
    position: absolute;
    width: 600px;
    height: 342px;
    box-shadow: 0 2px 6px rgba(0, 0, 0, 0.45);
  }
  .card-front {
    left: 302px;
    top: 129px;
    background: var(--card-white);
  }
  .card-back {
    left: 299px;
    top: 489px;
    background: linear-gradient(135deg, var(--slate-light) 0%, #4a4a4d 45%, var(--slate-dark) 100%);
  }
  .identity {
    position: absolute;
    left: 34px;
    top: 46px;
    display: flex;
    align-items: center;
    gap: 14px;
  }
  .identity-square {
    width: 44px;
    height: 44px;
    background: var(--brand-blue);
  }
  .person-name {
    font-size: 20px;
    font-weight: 700;
    color: var(--brand-blue);
    letter-spacing: 0.2px;
    line-height: 1.1;
  }
  .person-title {
    font-size: 15px;
    color: var(--title-gray);
    margin-top: 3px;
  }
  .contact {
    position: absolute;
    right: 35px;
    top: 257px;
    text-align: right;
    font-size: 13.5px;
    line-height: 18px;
    color: var(--text-gray);
  }
  .contact-label {
    font-weight: 700;
    color: var(--label-blue);
  }
  .company {
    position: absolute;
    left: 0;
    right: 0;
    top: 0;
    bottom: 0;
    display: flex;
    align-items: center;
    justify-content: center;
    gap: 16px;
  }
  .company-dot {
    width: 38px;
    height: 38px;
    border-radius: 50%;
    background: var(--brand-blue);
  }
  .company-name {
    font-size: 30px;
    font-weight: 700;
    color: var(--mark-white);
    letter-spacing: 2px;
  }
</style>
</head>
<body>
  <main class="stage">
    <section class="card card-front">
      <div class="identity">
        <div class="identity-square"></div>
        <div>
          <p class="person-name">DANIEL HARLOW</p>
          <p class="person-title">Property Manager</p>
        </div>
      </div>
      <div class="contact">
        <p><span class="contact-label">Phone</span>: 619-555-0142 <span class="contact-label">Fax</span>: 619-555-0187</p>
        <p>daniel@brookvaleestates.us | www.brookvaleestates.us</p>
        <p>2750 Harbor Ridge Drive #B210, San Diego, CA 92108</p>
      </div>
    </section>
    <section class="card card-back">
      <div class="company">
        <div class="company-dot"></div>
        <p class="company-name">BROOKVALE ESTATES LLC</p>
      </div>
    </section>
  </main>
</body>
</html>
```